Business Cards used to invite people to our church

We are a church and have need of a business card sized advertisement that allows our members to hand them out in order to invite people to the church. I need the front of the card to say "You're Invited" or "Come Check us out". with the service times on the back of the card later.
I have attached one of the OLD cards we have used in the past, but we want a complete makeover, into a more modern style that does not require the image.
I am also replacing the old logo with a newer "flat" logo which is attached.
Please use marketing colors. (blue or red or something that catches attention)
Create a card that DOES NOT have the picture of the two people on the front
The information on the sample card back is correct to go onto new card
Target Market(s)
anyone
Industry/Entity Type
Business
Contact Information for Business Card
sertice times and address information which you can get from the sample card I uploaded. It should have "You're Invited" or "Come Check us out" on the front of the card with out logo.

```html
<!DOCTYPE html>
<html lang="en">
<head>
<meta charset="utf-8">
<title>Grace Harbor Ministries – Invitation Card</title>
<link href="https://fonts.googleapis.com/css2?family=Overpass:wght@300;700&display=swap" rel="stylesheet">
<style>
  :root {
    --page: #ffffff;
    --navy: #28347c;
    --navy-soft: #34428c;
    --navy-deep: #222c6e;
    --band-red: #c8202f;
    --white: #ffffff;
  }
  html, body {
    margin: 0;
    padding: 0;
    width: 1200px;
    height: 1000px;
    overflow: hidden;
    background: var(--page);
  }
  .canvas {
    position: relative;
    width: 1200px;
    height: 1000px;
  }
  .invite-card {
    position: absolute;
    left: 55px;
    top: 167px;
    width: 1089px;
    height: 637px;
    overflow: hidden;
    background: var(--navy);
  }
  .worship-photo {
    position: absolute;
    inset: 0;
    background:
      radial-gradient(ellipse 40% 60% at 70% 45%, rgba(90, 90, 160, 0.45), transparent 70%),
      radial-gradient(ellipse 30% 50% at 25% 55%, rgba(70, 85, 150, 0.35), transparent 70%),
      linear-gradient(100deg, var(--navy-deep) 0%, var(--navy) 45%, var(--navy-soft) 100%);
  }
  .lockup {
    position: absolute;
    left: 240px;
    top: 176px;
    display: flex;
    align-items: center;
    gap: 36px;
  }
  .lockup-mark {
    width: 70px;
    height: 70px;
    background: var(--white);
  }
  .ministry-name {
    margin: 0;
    font-family: "Overpass", sans-serif;
    font-weight: 700;
    font-size: 52px;
    line-height: 63px;
    color: var(--white);
    letter-spacing: 0.5px;
  }
  .ministry-name span { display: block; }
  .invite-band {
    position: absolute;
    left: 0;
    top: 406px;
    width: 100%;
    height: 68px;
    background: linear-gradient(90deg,
      rgba(200, 32, 47, 0.05) 0%,
      rgba(200, 32, 47, 0.55) 12%,
      var(--band-red) 30%,
      var(--band-red) 68%,
      rgba(200, 32, 47, 0.55) 88%,
      rgba(200, 32, 47, 0.1) 100%);
    display: flex;
    align-items: center;
    justify-content: center;
  }
  .invite-line {
    margin: 0;
    font-family: "Overpass", sans-serif;
    font-weight: 300;
    font-size: 40px;
    letter-spacing: 20px;
    color: var(--white);
    transform: translateX(-50px);
  }
</style>
</head>
<body>
  <div class="canvas">
    <section class="invite-card">
      <div class="worship-photo" role="img" aria-label="Photograph of a congregation worshipping, tinted deep blue"></div>

      <div class="lockup">
        <div class="lockup-mark"></div>
        <h1 class="ministry-name">
          <span>Grace</span>
          <span>Harbor</span>
          <span>Ministries</span>
        </h1>
      </div>

      <div class="invite-band">
        <p class="invite-line">you are invited</p>
      </div>
    </section>
  </div>
</body>
</html>
```